Financial Services Consultant needs a business card

We need a business card for a new consulting company based in Melbourne called
"Quelbrook Insights". Tagline is Track, Review, Gain
We would like to see business card designs that are in line with the minimal style of the website www.quelbrook-insights.example
The font I have used on the website is Proxima Nova and would like the same or similar font used on the business card with a minimal design in line with the website Two sided with "QUELBROOK INSIGHTS" TRACK, REVIEW, GAIN on one side and name, title and contact details on the otther
Updates

Hi All, thanks for your submissions, much appreciated.

I have recently added some colour to my webiste, it is hex #3a7b74 for those that wish to use it
Thanks

Hi all

thanks very much for your design submissions I am very impressed and they are much appreciated.

Interms of general feedback please find below;

Colour: I am trying to stick to a minimal design and colour scheme for my website which is still under construction, up to 3 colours( www.quelbrook-insights.example) it is currently black and white with a small amount of blue/green but I am open to suggestion/interpretations for a consulting company.

Card: I dont mind if it has rounded edges or straight, I was thinking about using a letterpress card if possible

Detail: the detail on the card will include; Name, Title, Mobile, Personal Email, Business Email,Web,Business Address

Once again thanks for submissions

Industry/Entity Type

Business

```html
<!DOCTYPE html>
<html lang="en">
<head>
<meta charset="utf-8">
<title>Quelbrook Insights – Business Card</title>
<link rel="stylesheet" href="https://fonts.googleapis.com/css2?family=Montserrat:wght@600;700&family=Open+Sans:wght@400;600&display=swap">
<style>
  :root {
    --backdrop: #e9e6e1;
    --card: #ffffff;
    --ink: #111111;
    --band: #141213;
    --teal: #3a7b74;
    --muted: #555555;
    --soft-ink: #333333;
    --frame: #c9c9c9;
    --shadow: rgba(0, 0, 0, 0.18);
  }
  * { box-sizing: border-box; margin: 0; padding: 0; }
  html, body {
    width: 1200px;
    height: 720px;
    overflow: hidden;
    background: var(--backdrop);
  }
  .canvas {
    position: relative;
    width: 1200px;
    height: 720px;
    display: flex;
    align-items: center;
    justify-content: center;
    gap: 40px;
  }
  .card {
    position: relative;
    width: 540px;
    height: 309px;
    background: var(--card);
    box-shadow: 0 6px 18px var(--shadow);
    overflow: hidden;
  }
  .wordmark {
    position: absolute;
    border: 1px solid var(--frame);
    font-family: "Montserrat", sans-serif;
    font-weight: 700;
    color: var(--ink);
    white-space: nowrap;
    line-height: 1;
  }

  /* Details side */
  .card--details .wordmark {
    left: 40px;
    top: 52px;
    padding: 8px 12px;
    font-size: 24px;
    letter-spacing: 3px;
    background: var(--card);
    z-index: 2;
  }
  .rule {
    position: absolute;
    left: 0;
    right: 0;
    height: 2px;
    background: var(--teal);
  }
  .rule--top { top: 106px; }
  .rule--bottom { top: 156px; }
  .name-band {
    position: absolute;
    left: 0;
    right: 0;
    top: 112px;
    height: 38px;
    background: var(--band);
    display: flex;
    align-items: center;
    justify-content: center;
    padding-left: 70px;
    font-family: "Open Sans", sans-serif;
    color: #ffffff;
  }
  .name-band .person { font-size: 17px; font-weight: 600; }
  .name-band .title { font-size: 13px; font-weight: 400; margin-left: 4px; }
  .contact {
    position: absolute;
    top: 190px;
    left: 0;
    right: 0;
    display: flex;
    justify-content: center;
    font-family: "Open Sans", sans-serif;
    font-size: 12.5px;
    color: var(--muted);
    line-height: 1.6;
  }
  .contact__address {
    text-align: right;
    padding: 14px 12px 0 0;
    border-right: 1px solid var(--frame);
  }
  .contact__lines { padding-left: 10px; }
  .contact__line { display: flex; align-items: center; gap: 6px; }
  .contact__line svg { width: 11px; height: 11px; flex: none; }

  /* Brand side */
  .card--brand .wordmark {
    left: 50%;
    top: 88px;
    transform: translateX(-50%);
    padding: 10px 14px 30px;
    font-size: 30px;
    letter-spacing: 3.5px;
  }
  .tagline {
    position: absolute;
    right: 14px;
    bottom: 8px;
    font-family: "Open Sans", sans-serif;
    font-weight: 400;
    font-size: 14px;
    letter-spacing: 0.3px;
    color: var(--soft-ink);
  }
  .web {
    position: absolute;
    left: 0;
    right: 0;
    top: 222px;
    text-align: center;
    font-family: "Open Sans", sans-serif;
    font-size: 15px;
    letter-spacing: 3px;
    color: var(--soft-ink);
  }
  .web strong { font-weight: 600; color: var(--ink); }
</style>
</head>
<body>
<main class="canvas">
  <section class="card card--details" aria-label="Card side with name and contact details">
    <div class="wordmark">QUELBROOK INSIGHTS</div>
    <div class="rule rule--top"></div>
    <div class="name-band">
      <span class="person">Your Name,</span><span class="title">Title</span>
    </div>
    <div class="rule rule--bottom"></div>
    <div class="contact">
      <div class="contact__address">
        Street Name, City Name<br>State Zip Code
      </div>
      <div class="contact__lines">
        <div class="contact__line">
          <svg viewBox="0 0 12 12" aria-hidden="true">
            <circle cx="6" cy="6" r="5.3" fill="none" stroke="#555" stroke-width="1"/>
            <path d="M4 3.2 L5 3 L5.6 4.6 L5 5.1 Q5.6 6.5 6.9 7 L7.4 6.4 L9 7 L8.8 8 Q6.2 8.6 3.9 5.6 Q3.5 4.2 4 3.2 Z" fill="#555"/>
          </svg>
          <span>555-014-2276</span>
        </div>
        <div class="contact__line">
          <svg viewBox="0 0 12 12" aria-hidden="true">
            <circle cx="6" cy="6" r="5.5" fill="#777"/>
            <circle cx="6" cy="6" r="3.4" fill="none" stroke="#fff" stroke-width="0.8"/>
            <path d="M2.6 6 H9.4 M6 2.6 V9.4" stroke="#fff" stroke-width="0.7"/>
          </svg>
          <span>www.quelbrook-insights.example</span>
        </div>
      </div>
    </div>
  </section>

  <section class="card card--brand" aria-label="Card side with company name and tagline">
    <div class="wordmark">
      QUELBROOK INSIGHTS
      <span class="tagline">Track, Review, Gain</span>
    </div>
    <p class="web">www.<strong>quelbrook-insights</strong>.example</p>
  </section>
</main>
</body>
</html>
```